Business Card for a mobile physiotherapy company

I need a layout for a business card for a mobile physiotherapy company.
Slogan is "Mobile Physiotherapy - Your Road To Recovery"
Phone number is 867-555-0142
Email VardenTherapy@postnest.ca (subject to change with website)
Website www.VardenTherapy.ca
My name and credentials: Luke Varden Luke Varden, BSc(kin), MPT, CAFCI, IMS
Information maybe included: Direct Billing, Services including Physiotherapy, IMS, acupuncture
Maybe include facebook and instagram logos
One side with the logo clean and sharp
Other side with details, try not to look too busy, keep everything concise

```html
<!DOCTYPE html>
<html lang="en">
<head>
<meta charset="utf-8">
<title>Varden Therapy – Business Card</title>
<link href="https://fonts.googleapis.com/css2?family=Lato:wght@400;700&family=Roboto:wght@400&display=swap" rel="stylesheet">
<style>
  :root {
    --stage: #9a9a9a;
    --green: #17594f;
    --green-light: #1e6a5e;
    --navy: #2f4a7d;
    --white: #ffffff;
    --text-green: #1c5b4f;
  }
  html, body { margin: 0; padding: 0; }
  body {
    width: 1200px; height: 930px; overflow: hidden;
    background: radial-gradient(circle at 55% 35%, #c4c4c4, var(--stage) 75%);
    font-family: "Lato", sans-serif;
    position: relative;
  }
  .card {
    position: absolute; left: 270px;
    width: 660px; height: 400px;
    border-radius: 28px; overflow: hidden;
    box-shadow: 0 10px 24px rgba(0,0,0,.3);
  }
  .card--front {
    top: 40px;
    background: linear-gradient(135deg, var(--green-light), var(--green));
    color: var(--white);
    display: flex; flex-direction: column; align-items: center; justify-content: center;
  }
  .brand { display: flex; align-items: center; gap: 12px; }
  .brand__name {
    font-family: "Lato", sans-serif; font-weight: 700;
    font-size: 46px; letter-spacing: 4px; text-transform: uppercase; line-height: 1;
  }
  .brand__sub {
    font-family: "Lato", sans-serif; font-weight: 700;
    font-size: 22px; letter-spacing: 14px; text-transform: uppercase; margin-top: 10px; text-align: center;
  }
  .slogan { margin: 70px 0 0; font-size: 19px; letter-spacing: .3px; }

  .card--back { top: 490px; background: var(--white); }
  .card__wave { position: absolute; inset: 0; width: 100%; height: 100%; }
  .back-brand {
    position: absolute; right: 40px; top: 180px; color: var(--navy);
    display: flex; flex-direction: column; align-items: center;
  }
  .back-brand .brand__name { font-size: 40px; }
  .back-brand .brand__sub { font-size: 19px; letter-spacing: 12px; }
  .details { position: absolute; left: 44px; top: 210px; }
  .details__name {
    font-family: "Roboto", sans-serif; font-weight: 400; color: var(--navy);
    font-size: 24px; line-height: 1.1; margin: 0;
  }
  .details__services { color: var(--text-green); font-size: 13.5px; line-height: 1.35; margin: 6px 0 10px; }
  .contact { list-style: none; margin: 0; padding: 0; color: var(--text-green); font-size: 14.5px; }
  .contact li { display: flex; align-items: center; gap: 10px; line-height: 1.55; }
  .contact svg { width: 12px; height: 12px; fill: var(--navy); flex: none; }
</style>
</head>
<body>
  <section class="card card--front" aria-label="Card front">
    <div class="brand"><span class="brand__name">Varden</span></div>
    <div class="brand__sub">Therapy</div>
    <p class="slogan">Mobile Physiotherapy - Your Road To Recovery</p>
  </section>

  <section class="card card--back" aria-label="Card back">
    <svg class="card__wave" viewBox="0 0 660 400" preserveAspectRatio="none" aria-hidden="true">
      <path d="M0,0 H660 V70 C520,120 420,128 330,134 C220,142 100,148 0,170 Z" fill="var(--green)"/>
      <path d="M660,70 C520,120 420,128 330,134 C220,142 100,148 0,170" fill="none" stroke="var(--white)" stroke-width="8"/>
      <path d="M660,78 C520,130 420,138 330,144 C220,152 100,158 0,181" fill="none" stroke="var(--navy)" stroke-width="8"/>
      <path d="M660,86 C520,138 420,147 330,153 C220,161 100,167 0,191" fill="none" stroke="var(--white)" stroke-width="4"/>
    </svg>

    <div class="back-brand">
      <div class="brand"><span class="brand__name">Varden</span></div>
      <div class="brand__sub">Therapy</div>
    </div>

    <div class="details">
      <h1 class="details__name">Luke Varden, BSc(kin),<br>MPT, CAFCI, IMS</h1>
      <p class="details__services">Direct Billing, Services including<br>Physiotherapy, IMS, acupuncture</p>
      <ul class="contact">
        <li><svg viewBox="0 0 24 24"><path d="M6.6 10.8a15 15 0 0 0 6.6 6.6l2.2-2.2a1 1 0 0 1 1-.25 11.4 11.4 0 0 0 3.6.6 1 1 0 0 1 1 1V20a1 1 0 0 1-1 1A17 17 0 0 1 3 4a1 1 0 0 1 1-1h3.5a1 1 0 0 1 1 1c0 1.25.2 2.45.6 3.6a1 1 0 0 1-.25 1z"/></svg>867-555-0142</li>
        <li><svg viewBox="0 0 24 24"><path d="M2 5h20v14H2z M4 7v1l8 5 8-5V7l-8 5z" fill-rule="evenodd"/></svg>VardenTherapy@postnest.ca</li>
        <li><svg viewBox="0 0 24 24"><path d="M12 2a10 10 0 1 0 0 20 10 10 0 0 0 0-20zm6.9 6h-3a15 15 0 0 0-1.3-3.9A8 8 0 0 1 18.9 8zM12 4c.8 1.2 1.5 2.5 1.9 4h-3.8c.4-1.5 1.1-2.8 1.9-4zM4.3 14a8 8 0 0 1 0-4h3.4a16 16 0 0 0 0 4zm.8 2h3a15 15 0 0 0 1.3 3.9A8 8 0 0 1 5.1 16zm3-8h-3a8 8 0 0 1 4.3-3.9A15 15 0 0 0 8.1 8zM12 20c-.8-1.2-1.5-2.5-1.9-4h3.8c-.4 1.5-1.1 2.8-1.9 4zm2.3-6H9.7a14 14 0 0 1 0-4h4.6a14 14 0 0 1 0 4zm.3 5.9a15 15 0 0 0 1.3-3.9h3a8 8 0 0 1-4.3 3.9zm1.7-5.9a16 16 0 0 0 0-4h3.4a8 8 0 0 1 0 4z"/></svg>www.VardenTherapy.ca</li>
      </ul>
    </div>
  </section>
</body>
</html>
```